Wordpress website for Dance Studio

Hi there, I am looking for Wordpress Website for dance studio. Happy for designed to use available themes. Would like a few pages setup and I can do the rest.

Other things I would like included in this theme :

Nice images page OR moving banner
Blog
Ability for youtubes

Other than that, simple requirements, just a gorgeous looking landing page/site etc.

Target Market(s)

Dance mums and kids (dancers)

Industry/Entity Type

Dance and Performancer

Coding

Coded - Design and coding required

Number of Pages Required

4 page

Font styles to use
Sans Serif

Colors
EB3D1F
EC4F4E
F09395
F8D3D4
FCEDEE

Requirements
Must have
• Wordpress theme
Nice to have
• Artistic, graphical, dance studio theme

```html
<!DOCTYPE html>
<html lang="en">
<head>
<meta charset="utf-8">
<title>Step &amp; Sway Studio</title>
<link rel="stylesheet" href="https://fonts.googleapis.com/css2?family=Montserrat:wght@500;600;700;800&family=Open+Sans:wght@400;600&family=Dancing+Script:wght@500&display=swap">
<style>
:root{
  --brand:#EB3D1F;
  --brand-2:#EC4F4E;
  --blush:#F09395;
  --rose:#F8D3D4;
  --mist:#FCEDEE;
  --ink:#222222;
  --text:#444444;
  --white:#ffffff;
  --night:#000000;
}
*{box-sizing:border-box;margin:0;padding:0}
html,body{width:1200px;height:3394px;overflow:hidden}
body{position:relative;background:var(--white);font-family:"Open Sans",Arial,sans-serif;color:var(--text)}
.abs{position:absolute}
.heading{font-family:"Montserrat",Arial,sans-serif;font-weight:700;color:var(--ink)}
.script{font-family:"Dancing Script",cursive;color:var(--brand);font-size:22px}

/* header */
.site-header{left:0;top:0;width:1200px;height:74px;background:var(--brand)}
.brand{left:133px;top:22px;font-family:"Montserrat",sans-serif;font-weight:700;font-size:21px;color:var(--white);white-space:nowrap}
.nav{left:0;top:31px;width:100%}
.nav a{position:absolute;font-family:"Montserrat",sans-serif;font-weight:600;font-size:12px;color:var(--white);text-decoration:none;white-space:nowrap}
.call{left:863px;top:16px;width:42px;height:42px;border-radius:50%;background:var(--white)}
.call-label{left:910px;top:14px;font-size:12px;font-family:"Dancing Script",cursive;color:var(--white)}
.call-number{left:909px;top:29px;font-family:"Montserrat",sans-serif;font-weight:700;font-size:24px;color:var(--white)}

/* hero */
.hero{left:0;top:74px;width:1200px;height:548px;background:linear-gradient(90deg,#f7f6f5 0%,#efeeec 45%,#e6e3e0 70%,#f2f1ef 100%)}
.hero-photo{left:640px;top:74px;width:460px;height:548px;background:radial-gradient(ellipse at 50% 45%,#d9cdc8 0%,#e9e4e1 55%,rgba(240,238,236,0) 80%)}
.hero-title{left:129px;top:226px;font-size:47px;line-height:52px;font-weight:800;letter-spacing:.5px;white-space:nowrap}
.hero-title span{color:var(--brand)}
.hero-text{left:129px;top:341px;width:520px;font-size:13px;line-height:28px;color:#333}
.btn{display:flex;align-items:center;justify-content:center;border-radius:30px;font-family:"Montserrat",sans-serif;font-weight:700;font-size:16px;text-decoration:none}
.btn-solid{background:linear-gradient(90deg,var(--brand-2),var(--brand));color:var(--white)}
.btn-light{background:var(--white);color:var(--brand)}
.dots{left:574px;top:581px;display:flex;gap:5px}
.dots i{width:9px;height:9px;border-radius:50%;background:#bdbdbd;display:block}
.dots i:first-child{background:var(--brand)}

/* section headings */
.section-head{width:1200px;left:0;text-align:center}
.section-head .heading{font-size:32px;letter-spacing:.5px}
.rule{width:38px;height:7px;background:var(--brand);margin:6px auto 0}

/* cards */
.card{width:300px;height:362px;background:var(--white);box-shadow:0 0 12px rgba(0,0,0,.08)}
.card.lift{box-shadow:0 0 16px rgba(0,0,0,.18)}
.card-media{position:absolute;left:6px;top:6px;width:288px;height:194px}
.play{position:absolute;left:129px;top:82px;width:32px;height:32px}
.card-title{position:absolute;left:16px;top:207px;font-size:16px;line-height:28px;font-weight:700;color:var(--ink);white-space:nowrap}
.card-text{position:absolute;left:16px;top:265px;width:275px;font-size:12px;line-height:28px;color:#555}

/* about */
.about-band{left:0;top:1629px;width:1200px;height:534px;background:linear-gradient(120deg,var(--brand) 0%,var(--brand-2) 55%,var(--brand) 100%)}
.about-frame{left:92px;top:1665px;width:468px;height:557px;background:var(--white);box-shadow:0 4px 18px rgba(0,0,0,.15)}
.about-photo{position:absolute;left:8px;top:8px;width:452px;height:541px;background:linear-gradient(160deg,#f1f0ef 0%,#e4e2e1 50%,#f6f5f4 100%)}
.about-label{left:600px;top:1692px;color:var(--white)}
.about-title{left:600px;top:1722px;font-size:32px;color:var(--white);font-weight:700;white-space:nowrap}
.about-rule{left:600px;top:1767px;width:38px;height:5px;background:var(--white)}
.about-text{left:600px;top:1795px;width:470px;font-size:13px;line-height:28px;color:var(--white)}

/* footer */
.site-footer{left:0;top:2845px;width:1200px;height:549px;background:var(--night)}
.mail-title{left:0;top:2922px;width:1200px;text-align:center;font-size:32px;color:var(--white);font-weight:800}
.mail-text{left:0;top:2978px;width:1200px;text-align:center;font-size:11px;color:var(--white)}
.mail-form{left:283px;top:3018px;width:600px;height:50px;border-radius:25px;background:var(--white);border:2px solid var(--brand)}
.mail-input{position:absolute;left:43px;top:16px;font-size:11px;color:#aaa}
.mail-btn{position:absolute;right:2px;top:2px;width:138px;height:42px}
.divider{left:107px;width:981px;height:1px;background:#555}
.foot-brand{left:121px;top:3168px;font-family:"Montserrat",sans-serif;font-weight:700;font-size:22px;color:var(--white);white-space:nowrap}
.social{left:148px;top:3229px;display:flex;gap:18px}
.social i{display:block;width:26px;height:26px;border-radius:50%;background:var(--brand)}
.foot-col{color:var(--white)}
.foot-col h4{font-family:"Montserrat",sans-serif;font-size:16px;font-weight:700;margin-bottom:9px;color:var(--white)}
.foot-col li{list-style:none;font-size:13px;line-height:28px;display:flex;align-items:center;gap:10px;padding-left:6px;color:var(--white);white-space:nowrap}
.foot-col li svg{flex:none}
.copyright{left:0;top:3331px;width:1200px;text-align:center;font-family:"Montserrat",sans-serif;font-weight:600;font-size:11px;color:var(--white)}
</style>
</head>
<body>

<header class="abs site-header" role="banner"></header>
<div class="abs brand">Step &amp; Sway Studio</div>
<nav class="abs nav">
  <a style="left:399px" href="#">HOME</a>
  <a style="left:467px" href="#">ABOUT US</a>
  <a style="left:559px" href="#">OUR PROGRAM</a>
  <a style="left:679px" href="#">BLOG</a>
  <a style="left:744px" href="#">CONTACT US</a>
</nav>
<div class="abs call"><svg width="42" height="42" viewBox="0 0 42 42"><path d="M15 13c1-1 2-1 3 0l2 3c.6 1 .3 2-.5 2.6l-1 .8c.8 2 2.5 3.8 4.5 4.6l.8-1c.6-.8 1.6-1.1 2.6-.5l3 2c1 1 1 2 0 3l-1.5 1.5c-5 1-14-8-13-13z" fill="#EB3D1F"/></svg></div>
<div class="abs call-label">Call Us Today</div>
<div class="abs call-number">123-456-7890</div>

<section class="abs hero" aria-label="Hero"></section>
<div class="abs hero-photo" role="img" aria-label="Dance teacher guiding a young ballerina in a bright studio"></div>
<h1 class="abs heading hero-title">WELCOME TO<br><span>STEP &amp; SWAY STUDIO</span></h1>
<p class="abs hero-text">Lorem ipsum dolor sit amet, consectetur adipiscing elit, sed do eiusmod tempor incididunt ut labore et dolore magna aliqua.</p>
<a class="abs btn btn-solid" style="left:129px;top:408px;width:187px;height:54px" href="#">WATCH VIDEO</a>
<div class="abs dots"><i></i><i></i><i></i><i></i></div>

<!-- programs -->
<div class="abs section-head" style="top:692px">
  <div class="script">Videos</div>
  <h2 class="heading">OUR DANCE PROGRAMS</h2>
  <div class="rule"></div>
</div>

<article class="abs card" style="left:132px;top:798px">
  <div class="card-media" role="img" aria-label="Teacher helping a young dancer at the barre" style="background:linear-gradient(135deg,#c9a58e,#efe2d8)"><svg class="play" viewBox="0 0 32 32"><circle cx="16" cy="16" r="16" fill="#EB3D1F"/><path d="M12 9l11 7-11 7z" fill="#fff"/></svg></div>
  <h3 class="card-title heading">LOREM IPSUM DOLOR SIT AMET<br>CONSECTETUR ADIPI.</h3>
  <p class="card-text">Lorem ipsum dolor sit amet, consectetur adip-iscing elit, sed do eiusmod tempor incididunt ut labore et dolore magna aliqua.</p>
</article>
<article class="abs card lift" style="left:450px;top:798px">
  <div class="card-media" role="img" aria-label="Group dance fitness class" style="background:linear-gradient(135deg,#e8b9a8,#c86a72)"><svg class="play" viewBox="0 0 32 32"><circle cx="16" cy="16" r="16" fill="#EB3D1F"/><path d="M12 9l11 7-11 7z" fill="#fff"/></svg></div>
  <h3 class="card-title heading">LOREM IPSUM DOLOR SIT AMET<br>CONSECTETUR ADIPI.</h3>
  <p class="card-text">Lorem ipsum dolor sit amet, consectetur adip-iscing elit, sed do eiusmod tempor incididunt ut labore et dolore magna aliqua.</p>
</article>
<article class="abs card" style="left:769px;top:798px">
  <div class="card-media" role="img" aria-label="Mother and daughter dancing together" style="background:linear-gradient(135deg,#3b2f2c,#d3a896)"><svg class="play" viewBox="0 0 32 32"><circle cx="16" cy="16" r="16" fill="#EB3D1F"/><path d="M12 9l11 7-11 7z" fill="#fff"/></svg></div>
  <h3 class="card-title heading">LOREM IPSUM DOLOR SIT AMET<br>CONSECTETUR ADIPI.</h3>
  <p class="card-text">Lorem ipsum dolor sit amet, consectetur adip-iscing elit, sed do eiusmod tempor incididunt ut labore et dolore magna aliqua.</p>
</article>

<article class="abs card" style="left:132px;top:1181px">
  <div class="card-media" role="img" aria-label="Little ballerina sitting on the studio floor" style="background:linear-gradient(135deg,#f3efec,#e6d3cf)"><svg class="play" viewBox="0 0 32 32"><circle cx="16" cy="16" r="16" fill="#EB3D1F"/><path d="M12 9l11 7-11 7z" fill="#fff"/></svg></div>
  <h3 class="card-title heading">LOREM IPSUM DOLOR SIT AMET<br>CONSECTETUR ADIPI.</h3>
  <p class="card-text">Lorem ipsum dolor sit amet, consectetur adip-iscing elit, sed do eiusmod tempor incididunt ut labore et dolore magna aliqua.</p>
</article>
<article class="abs card" style="left:450px;top:1181px">
  <div class="card-media" role="img" aria-label="Mother and child on stage by curtains" style="background:linear-gradient(90deg,#2f2a33,#5a4a52 60%,#d9a62a)"><svg class="play" viewBox="0 0 32 32"><circle cx="16" cy="16" r="16" fill="#EB3D1F"/><path d="M12 9l11 7-11 7z" fill="#fff"/></svg></div>
  <h3 class="card-title heading">LOREM IPSUM DOLOR SIT AMET<br>CONSECTETUR ADIPI.</h3>
  <p class="card-text">Lorem ipsum dolor sit amet, consectetur adip-iscing elit, sed do eiusmod tempor incididunt ut labore et dolore magna aliqua.</p>
</article>
<article class="abs card" style="left:769px;top:1181px">
  <div class="card-media" role="img" aria-label="Two young ballerinas in blue leotards" style="background:linear-gradient(135deg,#eef0f3,#6d86c4)"><svg class="play" viewBox="0 0 32 32"><circle cx="16" cy="16" r="16" fill="#EB3D1F"/><path d="M12 9l11 7-11 7z" fill="#fff"/></svg></div>
  <h3 class="card-title heading">LOREM IPSUM DOLOR SIT AMET<br>CONSECTETUR ADIPI.</h3>
  <p class="card-text">Lorem ipsum dolor sit amet, consectetur adip-iscing elit, sed do eiusmod tempor incididunt ut labore et dolore magna aliqua.</p>
</article>

<!-- about -->
<section class="abs about-band" aria-label="About"></section>
<div class="abs about-frame"><div class="about-photo" role="img" aria-label="Ballerina and small girl dancing by large windows"></div></div>
<div class="abs script about-label">About</div>
<h2 class="abs heading about-title">STEP &amp; SWAY STUDIO</h2>
<div class="abs about-rule"></div>
<p class="abs about-text">Lorem ipsum dolor sit amet, consectetur adipiscing elit, sed do eiusmod tempor incididunt ut labore et dolore magna aliqua. Quis ipsum suspendisse ultrices gravida. Risus commodo viverra maecenas accumsan lacus vel facilisis. Sed ut perspiciatis unde omnis iste natus error sit voluptatem accusantium doloremque laudantium, totam rem aperiam, eaque ipsa quae ab illo inventore veritatis et quasi architecto beatae vitae dicta sunt explicabo. Nemo enim ipsam voluptatem quia voluptas sit aspernatur aut odit aut fugit, sed quia consequuntur magni.</p>
<a class="abs btn btn-light" style="left:600px;top:2039px;width:189px;height:53px" href="#">LEARN MORE</a>

<!-- blog -->
<div class="abs section-head" style="top:2296px">
  <div class="script">Blog</div>
  <h2 class="heading">OUR LATEST BLOG</h2>
  <div class="rule"></div>
</div>

<article class="abs card" style="left:132px;top:2404px">
  <div class="card-media" role="img" aria-label="Teacher and young ballerina posing" style="background:linear-gradient(135deg,#f4f2f0,#e3cfcd)"></div>
  <h3 class="card-title heading">LOREM IPSUM DOLOR SIT AMET<br>CONSECTETUR ADIPI.</h3>
  <p class="card-text">Lorem ipsum dolor sit amet, consectetur adip-iscing elit, sed do eiusmod tempor incididunt ut labore et dolore magna aliqua.</p>
</article>
<article class="abs card lift" style="left:450px;top:2404px">
  <div class="card-media" role="img" aria-label="Two dancers stretching on the floor" style="background:linear-gradient(135deg,#f1f1f2,#8293c6)"></div>
  <h3 class="card-title heading">LOREM IPSUM DOLOR SIT AMET<br>CONSECTETUR ADIPI.</h3>
  <p class="card-text">Lorem ipsum dolor sit amet, consectetur adip-iscing elit, sed do eiusmod tempor incididunt ut labore et dolore magna aliqua.</p>
</article>
<article class="abs card" style="left:769px;top:2404px">
  <div class="card-media" role="img" aria-label="Ballerina and child in a white studio" style="background:linear-gradient(135deg,#efeeed,#dcd9d7)"></div>
  <h3 class="card-title heading">LOREM IPSUM DOLOR SIT AMET<br>CONSECTETUR ADIPI.</h3>
  <p class="card-text">Lorem ipsum dolor sit amet, consectetur adip-iscing elit, sed do eiusmod tempor incididunt ut labore et dolore magna aliqua.</p>
</article>

<!-- footer -->
<footer class="abs site-footer"></footer>
<h2 class="abs heading mail-title">JOIN OUR MAILING LIST</h2>
<p class="abs mail-text">Lorem ipsum dolor sit amet, consectetur adipiscing elit, sed do eiusmod tempor</p>
<form class="abs mail-form">
  <span class="mail-input">Enter Email Here</span>
  <span class="btn btn-solid mail-btn">SUBSCRIBE</span>
</form>
<div class="abs divider" style="top:3102px"></div>

<div class="abs foot-brand">Step &amp; Sway</div>
<div class="abs social" aria-label="Social links"><i></i><i></i><i></i><i></i></div>

<div class="abs foot-col" style="left:389px;top:3134px">
  <h4>QUICK LINKS</h4>
  <ul>
    <li><svg width="8" height="8" viewBox="0 0 8 8"><path d="M0 0l3 4-3 4M4 0l3 4-3 4" stroke="#fff" fill="none"/></svg>Home</li>
    <li><svg width="8" height="8" viewBox="0 0 8 8"><path d="M0 0l3 4-3 4M4 0l3 4-3 4" stroke="#fff" fill="none"/></svg>About Us</li>
    <li><svg width="8" height="8" viewBox="0 0 8 8"><path d="M0 0l3 4-3 4M4 0l3 4-3 4" stroke="#fff" fill="none"/></svg>Our program</li>
    <li><svg width="8" height="8" viewBox="0 0 8 8"><path d="M0 0l3 4-3 4M4 0l3 4-3 4" stroke="#fff" fill="none"/></svg>Blog</li>
    <li><svg width="8" height="8" viewBox="0 0 8 8"><path d="M0 0l3 4-3 4M4 0l3 4-3 4" stroke="#fff" fill="none"/></svg>Contact Us</li>
  </ul>
</div>
<div class="abs foot-col" style="left:624px;top:3134px">
  <h4>LEGAL</h4>
  <ul>
    <li><svg width="8" height="8" viewBox="0 0 8 8"><path d="M0 0l3 4-3 4M4 0l3 4-3 4" stroke="#fff" fill="none"/></svg>Terms of Use</li>
    <li><svg width="8" height="8" viewBox="0 0 8 8"><path d="M0 0l3 4-3 4M4 0l3 4-3 4" stroke="#fff" fill="none"/></svg>Privacy Policy</li>
    <li><svg width="8" height="8" viewBox="0 0 8 8"><path d="M0 0l3 4-3 4M4 0l3 4-3 4" stroke="#fff" fill="none"/></svg>FAQ</li>
    <li><svg width="8" height="8" viewBox="0 0 8 8"><path d="M0 0l3 4-3 4M4 0l3 4-3 4" stroke="#fff" fill="none"/></svg>Sitmap</li>
  </ul>
</div>
<div class="abs foot-col" style="left:830px;top:3134px">
  <h4>CONTACT US</h4>
  <ul>
    <li><svg width="10" height="12" viewBox="0 0 10 12"><path d="M5 0a4 4 0 0 1 4 4c0 3-4 8-4 8S1 7 1 4a4 4 0 0 1 4-4z" fill="#fff"/><circle cx="5" cy="4" r="1.5" fill="#000"/></svg>123 Lorem ipsum dolor sit amet</li>
    <li style="margin-top:6px"><svg width="12" height="12" viewBox="0 0 12 12"><path d="M2 1c.5-.5 1-.5 1.5 0l1.5 2c.3.5.2 1-.3 1.3l-.6.5c.5 1.3 1.6 2.4 2.9 2.9l.5-.6c.3-.5.8-.6 1.3-.3l2 1.5c.5.5.5 1 0 1.5l-1 1C6 12 0 6 1 2z" fill="#fff"/></svg>123 456 7890</li>
    <li style="margin-top:12px"><svg width="13" height="10" viewBox="0 0 13 10"><rect width="13" height="10" rx="1" fill="#fff"/><path d="M0 1l6.5 5L13 1" stroke="#000" fill="none"/></svg>info@stepandsway.example</li>
  </ul>
</div>

<div class="abs divider" style="top:3310px"></div>
<p class="abs copyright">© Copyrights 2021 Step &amp; Sway Studio &nbsp;|&nbsp;&nbsp; All Rights Reserved</p>

</body>
</html>
```